Kelvaro.ch is looking for business card letterhead and envelope C5 with WOW effect

We need a strong business card for our company Kelvaro.ch, logo is available. You want a black or dark background on which the logo Stark r% 26 # 252; appears. Letterhead and envelope in C5 format should be in a similar design, but does not have to be We need a strong business card for our company Kelvaro.ch, logo is available. A black or dark background is desired, on which the logo Stark comes across. The letterhead and the envelope in C5 format should have a similar design.

Target Market(s)

Private customers as well as entrepreneurs

Contact Information for Business Card

E-mail: info@kelvaro-example.ch
Web.www.Kelvaro-example.ch
Tel: +41 ( 0 ) 79 482 6037
Adresse:
Lindenweg 14
9406 Tarnbach

Hier kann man Icons verwenden für Email,Tel und Adressse

Font styles to use
Other font styles liked:
• Dubai,bold

Colors

Designer to choose colors to be used in the design.

Requirements
Must have
• WOW effect
Nice to have
• R% 26 # 252; back business card with our service listings. - VEHICLE LABELING - SHOP WINDOW LABELING - STICKERS AND MUCH MORE ... in red color

```html
<!DOCTYPE html>
<html lang="en">
<head>
<meta charset="utf-8">
<title>Kelvaro.ch business card</title>
<link href="https://fonts.googleapis.com/css2?family=Ubuntu:wght@400;500;700&display=swap" rel="stylesheet">
<style>
  :root{
    --backdrop:#4a433c;
    --card:#16203b;
    --card-light:#1d2a4a;
    --white:#ffffff;
    --yellow:#fcca1e;
    --red:#d8141e;
  }
  html,body{margin:0;padding:0;width:1200px;height:930px;overflow:hidden;background:var(--backdrop);}
  body{position:relative;font-family:"Ubuntu",sans-serif;color:var(--white);}
  .card{
    position:absolute;border-radius:18px;overflow:hidden;
    background:linear-gradient(135deg,var(--card) 0%,var(--card-light) 45%,var(--card) 100%);
    box-shadow:0 14px 30px rgba(0,0,0,.45);
  }
  .card--front{left:90px;top:100px;width:540px;height:320px;}
  .card--back{left:560px;top:500px;width:560px;height:330px;}

  .pattern-area{position:absolute;border-radius:6px;
    background:linear-gradient(135deg,#fcd43a,#f5be10);}
  .card--front .pattern-area{left:56px;top:96px;width:130px;height:120px;}
  .card--back .pattern-area{left:40px;top:70px;width:250px;height:220px;}

  .brand{font-weight:700;letter-spacing:1px;color:var(--white);margin:0;}
  .card--front .brand{position:absolute;left:216px;top:100px;font-size:38px;}
  .card--back .brand{position:absolute;right:34px;top:32px;font-size:34px;}

  .services{position:absolute;right:44px;top:160px;margin:0;padding:0;list-style:none;text-align:right;font-size:14px;line-height:20px;text-transform:uppercase;}
  .services li::after{content:"";display:inline-block;width:7px;height:7px;border:2px solid var(--red);border-radius:50%;margin-left:8px;vertical-align:middle;}

  .person{position:absolute;right:34px;top:112px;text-align:right;}
  .person__name{margin:0;font-size:24px;font-weight:700;letter-spacing:1.5px;}
  .person__name .surname{color:var(--yellow);}
  .person__role{margin:2px 0 0;font-size:15px;}
  .rule{position:absolute;right:34px;top:178px;width:70px;height:2px;background:var(--yellow);}

  .contacts{position:absolute;right:34px;top:196px;margin:0;padding:0;list-style:none;text-align:right;font-size:15px;line-height:22px;}
  .contacts svg{width:12px;height:12px;margin-left:8px;vertical-align:-1px;}
  .address{position:absolute;right:34px;top:272px;margin:0;font-size:15px;}
</style>
</head>
<body>

<section class="card card--front">
  <div class="pattern-area" role="img" aria-label="Yellow honeycomb hexagon pattern"></div>
  <p class="brand">KELVARO.CH</p>
  <ul class="services">
    <li>Vehicle labeling</li>
    <li>Shop window labeling</li>
    <li>Stickers and much more</li>
  </ul>
</section>

<section class="card card--back">
  <div class="pattern-area" role="img" aria-label="Large yellow honeycomb hexagon pattern"></div>
  <p class="brand">KELVARO.CH</p>
  <div class="person">
    <p class="person__name">JONAS <span class="surname">KELLER</span></p>
    <p class="person__role">Director</p>
  </div>
  <div class="rule"></div>
  <ul class="contacts">
    <li>+41 ( 0 ) 79 482 6037<svg viewBox="0 0 12 12"><path d="M2.5 1l2 2.5-1.2 1.2a7 7 0 0 0 4 4L8.5 7.5 11 9.5 9.8 11C5 11 1 7 1 2.2z" fill="var(--yellow)"/></svg></li>
    <li>info@kelvaro-example.ch<svg viewBox="0 0 12 12"><rect x="1" y="2.5" width="10" height="7" fill="none" stroke="var(--yellow)" stroke-width="1.3"/><path d="M1 2.5l5 4 5-4" fill="none" stroke="var(--yellow)" stroke-width="1.3"/></svg></li>
    <li>www.kelvaro-example.ch<svg viewBox="0 0 12 12"><circle cx="6" cy="6" r="5" fill="none" stroke="var(--yellow)" stroke-width="1.3"/><ellipse cx="6" cy="6" rx="2" ry="5" fill="none" stroke="var(--yellow)" stroke-width="1"/><path d="M1 6h10" stroke="var(--yellow)" stroke-width="1"/></svg></li>
  </ul>
  <p class="address">Lindenweg 14 9406 Tarnbach</p>
</section>

</body>
</html>
```